Maple Grove Schools | brand new stationery!

We need stationery design with our new logo! Our company updated it's name and image and we like to incorporate the new one on our stationery, business cards and email signature. We are looking for fresh, new ideas!
Industry: Childcare, Elementary and Middle School
Company Name: Maple Grove Schools
Tagline: Bright Futures Start Here
Main colors: Blue, white and a little yellow
Star shape is something new for us! Do you see a way to incorporate it as a design element?

```html
<!DOCTYPE html>
<html lang="en">
<head>
<meta charset="utf-8">
<title>Maple Grove Schools — Presentation Folder</title>
<link rel="stylesheet" href="https://fonts.googleapis.com/css2?family=Poppins:wght@600;700&family=Roboto:wght@400&display=swap">
<style>
  :root {
    --navy: #23286f;
    --navy-deep: #1b1f58;
    --navy-pattern: #2f3585;
    --navy-faint: #2e3374;
    --yellow: #f5bd1f;
    --white: #ffffff;
    --paper-shade: #e6e6e9;
    --ink: #1c1b1f;
    --muted-text: #c9cbe6;
    --backdrop: #d3d2d4;
  }
  * { box-sizing: border-box; margin: 0; padding: 0; }
  html, body { width: 1200px; height: 847px; overflow: hidden; }
  body {
    background: var(--backdrop);
    font-family: "Roboto", Arial, sans-serif;
    position: relative;
  }
  .folder {
    position: absolute;
    left: 30px; top: 43px;
    width: 1140px; height: 760px;
    display: flex;
  }
  .folder-panel {
    position: relative;
    width: 570px; height: 760px;
    overflow: hidden;
  }

  /* Back cover */
  .back-cover {
    background: linear-gradient(100deg, var(--navy-deep) 0%, var(--navy) 45%, var(--navy-deep) 100%);
  }
  .back-emblem {
    position: absolute;
    left: 135px; top: 150px;
    width: 300px; height: 300px;
    border-radius: 50%;
    background: var(--navy-faint);
    opacity: 0.85;
    display: flex;
    align-items: center;
    justify-content: center;
    text-align: center;
  }
  .back-emblem-name {
    font-family: "Poppins", Arial, sans-serif;
    font-weight: 600;
    font-size: 38px;
    line-height: 1.1;
    color: var(--navy-deep);
  }
  .back-address {
    position: absolute;
    right: 44px; bottom: 230px;
    text-align: right;
    font-style: normal;
    color: var(--muted-text);
    font-size: 12px;
    line-height: 1.45;
    letter-spacing: 0.3px;
  }
  .back-contacts {
    position: absolute;
    left: 50px; bottom: 48px;
    list-style: none;
    color: var(--muted-text);
    font-size: 12px;
    line-height: 1.55;
    letter-spacing: 0.3px;
  }
  .back-contacts li { display: flex; align-items: center; gap: 6px; }
  .contact-icon { width: 10px; height: 10px; flex: none; }

  /* Front cover */
  .front-cover {
    background: linear-gradient(90deg, var(--white) 0%, var(--white) 50%, var(--paper-shade) 100%);
  }
  .cover-bands { position: absolute; inset: 0; }
  .brand-lockup {
    position: absolute;
    left: 0; right: 0; top: 270px;
    display: flex;
    flex-direction: column;
    align-items: center;
    gap: 14px;
  }
  .brand-mark {
    width: 64px; height: 64px;
    border-radius: 50%;
    background: var(--navy);
  }
  .brand-name {
    text-align: center;
    font-family: "Poppins", Arial, sans-serif;
    font-weight: 600;
    color: var(--ink);
    font-size: 42px;
    line-height: 1.08;
    letter-spacing: -0.3px;
  }
  .brand-name span { display: block; }
  .tagline {
    position: absolute;
    left: 0; right: 0; bottom: 95px;
    text-align: center;
    font-family: "Poppins", Arial, sans-serif;
    font-weight: 700;
    font-size: 14px;
    letter-spacing: 0.5px;
    color: var(--yellow);
  }
</style>
</head>
<body>
  <main class="folder">
    <section class="folder-panel back-cover" aria-label="Back cover">
      <div class="back-emblem" aria-hidden="true">
        <span class="back-emblem-name">Maple Grove<br>Schools</span>
      </div>
      <address class="back-address">
        Maple Grove Schools<br>
        48 Willow Bend Ave Suite 3<br>
        Fairview, OH 44106
      </address>
      <ul class="back-contacts">
        <li>
          <svg class="contact-icon" viewBox="0 0 10 10" aria-hidden="true"><path d="M2 1h2l1 2-1.2 1a5 5 0 0 0 2.2 2.2L7 5l2 1v2a1 1 0 0 1-1 1A7 7 0 0 1 1 2a1 1 0 0 1 1-1z" fill="var(--yellow)"/></svg>
          1-800-555-0147
        </li>
        <li>
          <svg class="contact-icon" viewBox="0 0 10 10" aria-hidden="true"><rect x="0.5" y="2" width="9" height="6" fill="var(--yellow)"/><path d="M0.5 2 5 5.5 9.5 2" stroke="var(--navy)" fill="none" stroke-width="0.9"/></svg>
          hello@maplegroveschools.org
        </li>
        <li>
          <svg class="contact-icon" viewBox="0 0 10 10" aria-hidden="true"><circle cx="5" cy="5" r="4.5" fill="var(--yellow)"/><path d="M0.5 5h9M5 0.5c-2 2.5-2 6.5 0 9M5 0.5c2 2.5 2 6.5 0 9" stroke="var(--navy)" fill="none" stroke-width="0.7"/></svg>
          www.maplegroveschools.org
        </li>
      </ul>
    </section>

    <section class="folder-panel front-cover" aria-label="Front cover">
      <svg class="cover-bands" viewBox="0 0 570 760" width="570" height="760">
        <defs>
          <linearGradient id="band-tone" x1="0" y1="0" x2="1" y2="1">
            <stop offset="0" stop-color="var(--navy-pattern)"/>
            <stop offset="0.5" stop-color="var(--navy)"/>
            <stop offset="1" stop-color="var(--navy-pattern)"/>
          </linearGradient>
        </defs>
        <path d="M0 0H570V50C420 140 220 175 0 168Z" fill="url(#band-tone)" role="img" aria-label="Top band with a repeating star pattern"/>
        <path d="M0 178C220 186 420 150 570 62V78C420 162 220 196 0 186Z" fill="var(--yellow)"/>
        <path d="M0 612C220 600 420 562 570 520V528C420 570 220 608 0 620Z" fill="var(--yellow)"/>
        <path d="M0 632C220 618 420 580 570 534V760H0Z" fill="url(#band-tone)" role="img" aria-label="Bottom band with a repeating star pattern"/>
      </svg>
      <div class="brand-lockup">
        <span class="brand-mark" aria-hidden="true"></span>
        <h1 class="brand-name"><span>Maple Grove</span><span>Schools</span></h1>
      </div>
      <p class="tagline">Bright Futures Start Here</p>
    </section>
  </main>
</body>
</html>
```